Maple Grove Schools | brand new stationery!

We need stationery design with our new logo! Our company updated it's name and image and we like to incorporate the new one on our stationery, business cards and email signature. We are looking for fresh, new ideas!
Industry: Childcare, Elementary and Middle School
Company Name: Maple Grove Schools
Tagline: Bright Futures Start Here
Main colors: Blue, white and a little yellow
Star shape is something new for us! Do you see a way to incorporate it as a design element?

```html
<!DOCTYPE html>
<html lang="en">
<head>
<meta charset="utf-8">
<title>Maple Grove Schools – Presentation Folder</title>
<link rel="stylesheet" href="https://fonts.googleapis.com/css2?family=Lexend:wght@700&family=Roboto:wght@400&display=swap">
<style>
  :root {
    --navy: #24296b;
    --navy-deep: #1c1f52;
    --navy-light: #3a3c78;
    --gold: #e2ad17;
    --ink: #1f1d22;
    --paper: #ffffff;
    --backdrop: #cfcfd1;
  }
  * { margin: 0; padding: 0; box-sizing: border-box; }
  html, body {
    width: 1200px; height: 847px; overflow: hidden;
    background: var(--backdrop);
  }
  .folder {
    position: absolute; left: 75px; top: 73px;
    width: 1050px; height: 700px;
    display: flex;
    box-shadow: 0 10px 30px rgba(0,0,0,0.18);
  }
  .panel { position: relative; width: 525px; height: 700px; overflow: hidden; }

  /* Back cover */
  .back-cover {
    background: linear-gradient(160deg, var(--navy-light) 0%, var(--navy) 45%, var(--navy-deep) 100%);
  }
  .pattern-area {
    position: absolute; left: 0; top: 0; width: 100%; height: 210px;
    background: linear-gradient(180deg, rgba(255,255,255,0.07) 0%, rgba(255,255,255,0) 100%);
  }
  .contact-block {
    position: absolute; left: 0; right: 0; top: 560px;
    text-align: center; color: var(--paper);
    font-family: 'Roboto', sans-serif; font-size: 12.5px; line-height: 1.45;
    letter-spacing: 0.2px;
  }
  .contact-line svg { vertical-align: -2px; margin-right: 4px; }
  .contact-line .gap { display: inline-block; width: 10px; }

  /* Front cover */
  .front-cover { background: var(--paper); }
  .front-art { position: absolute; inset: 0; }
  .brand {
    position: absolute; left: 0; right: 0; top: 215px;
    text-align: center;
  }
  .brand-dot {
    width: 58px; height: 58px; border-radius: 50%;
    background: var(--navy); margin: 0 auto 26px;
  }
  .brand-name {
    font-family: 'Lexend', sans-serif; font-weight: 700;
    color: var(--ink); font-size: 40px; line-height: 1.1;
  }
  .tagline {
    position: absolute; left: 0; right: 0; top: 650px;
    text-align: center;
    font-family: 'Lexend', sans-serif; font-weight: 700;
    font-size: 14px; letter-spacing: 0.6px; color: var(--gold);
  }
</style>
</head>
<body>
  <div class="folder">
    <section class="panel back-cover">
      <div class="pattern-area" role="img" aria-label="Faint repeating star pattern"></div>
      <div class="contact-block">
        <p class="contact-line">Maple Grove Schools</p>
        <p class="contact-line">48 Birchwood Ave Suite 5 Fairhaven, OH 44120</p>
        <p class="contact-line">
          <svg width="11" height="10" viewBox="0 0 11 10" aria-hidden="true"><path d="M1 3 Q5.5 -1 10 3 L8.5 4.5 L7 3.5 L4 3.5 L2.5 4.5 Z M2.5 5 L8.5 5 L9.5 9.5 L1.5 9.5 Z" fill="var(--gold)"/></svg>1-800-555-0147<span class="gap"></span>
          <svg width="11" height="8" viewBox="0 0 11 8" aria-hidden="true"><rect x="0" y="0" width="11" height="8" fill="var(--gold)"/><path d="M0.5 0.5 L5.5 4.5 L10.5 0.5" stroke="var(--navy)" stroke-width="1" fill="none"/></svg>hello@maplegroveschools.org
        </p>
        <p class="contact-line">www.maplegroveschools.org</p>
      </div>
    </section>

    <section class="panel front-cover">
      <svg class="front-art" width="525" height="700" viewBox="0 0 525 700" aria-hidden="true">
        <defs>
          <linearGradient id="sheen" x1="0" y1="0" x2="1" y2="1">
            <stop offset="0" stop-color="#ffffff"/>
            <stop offset="1" stop-color="#ececec"/>
          </linearGradient>
        </defs>
        <rect width="525" height="700" fill="url(#sheen)"/>
        <path class="gold-swoosh" d="M170 612 Q370 628 525 520 L525 534 Q380 640 170 616 Z" fill="var(--gold)"/>
        <path class="navy-band" d="M0 505 Q250 660 525 545 L525 700 L0 700 Z" fill="var(--navy)"/>
      </svg>
      <div class="brand">
        <div class="brand-dot"></div>
        <p class="brand-name">Maple Grove<br>Schools</p>
      </div>
      <p class="tagline">Bright Futures Start Here</p>
    </section>
  </div>
</body>
</html>
```